Corvel Capital LLC

Need Professional Business cards for New Investment Fund

Target Market(s)

High Quality investors

Industry/Entity Type

Financial

Contact Information for Business Card

Phone Number +1 555 284 6190
Name Lukas Varenko
Title Fund Manager
email lv@FundCorvel.com
Website www.FundCorvel.com

Colors

Designer to choose colors to be used in the design.

Requirements
Must have
• Must have our Logo and all of the above. Must be made so lettering and loge can be raised

```html
<!DOCTYPE html>
<html lang="en">
<head>
<meta charset="utf-8">
<title>Quenvar — Business Card</title>
<link rel="stylesheet" href="https://fonts.googleapis.com/css2?family=Roboto:wght@400;500;700&display=swap">
<style>
  :root {
    --backdrop: #2a2a2a;
    --card: #161616;
    --card-front: #1a1a1a;
    --emboss: #3b3b3b;
    --white: #f2f2f2;
    --text-soft: #e4e4e4;
    --lime: #8cc21f;
    --band-dark: #3a4a3c;
    --band-mid: #5a7040;
    --rule: #d8d8d8;
  }
  * { margin: 0; padding: 0; box-sizing: border-box; }
  html, body {
    width: 1200px; height: 1138px; overflow: hidden;
    background: var(--backdrop);
    font-family: "Roboto", Arial, sans-serif;
  }
  .card {
    position: absolute;
    left: 276px;
    width: 620px;
    height: 374px;
    border-radius: 16px;
    overflow: hidden;
  }
  .card--front { top: 186px; background: var(--card-front); }
  .card--back  { top: 608px; background: var(--card); }

  .front-wordmark {
    position: absolute;
    left: 0; right: 0; top: 150px;
    text-align: center;
    font-weight: 500;
    font-size: 60px;
    line-height: 1;
    letter-spacing: 2px;
    color: var(--emboss);
  }

  .back-brand {
    position: absolute;
    left: 42px; top: 74px;
    display: flex; align-items: center; gap: 12px;
  }
  .back-brand__mark {
    width: 16px; height: 40px;
    background: var(--lime);
  }
  .back-brand__name {
    font-weight: 500;
    font-size: 44px;
    letter-spacing: 1px;
    color: var(--white);
    line-height: 1;
  }

  .contact-band {
    position: absolute;
    left: 13px; top: 170px;
    width: 594px; height: 190px;
    background:
      radial-gradient(circle at 94% 12%, var(--lime) 0%, var(--band-mid) 38%, transparent 75%),
      linear-gradient(90deg, var(--band-dark) 0%, #4a5e3e 60%, var(--band-mid) 100%);
  }
  .holder__name {
    position: absolute; left: 30px; top: 20px;
    font-weight: 700; font-size: 24px; line-height: 1.2; color: var(--text-soft);
  }
  .holder__title {
    position: absolute; left: 30px; top: 54px;
    font-size: 16px; line-height: 1.2; color: var(--text-soft);
  }
  .contact-list {
    position: absolute; left: 30px; top: 100px;
    width: 310px; list-style: none;
  }
  .contact-list li {
    display: flex; align-items: center; gap: 14px;
    height: 26px;
    font-size: 14.5px; color: var(--white);
  }
  .contact-list li + li { border-top: 1.5px solid var(--rule); }
  .contact-list svg { width: 16px; height: 14px; fill: var(--white); flex: none; }
</style>
</head>
<body>

<section class="card card--front" aria-label="Card front">
  <div class="front-wordmark">QUENVAR</div>
</section>

<section class="card card--back" aria-label="Card back">
  <div class="back-brand">
    <span class="back-brand__mark"></span>
    <span class="back-brand__name">QUENVAR</span>
  </div>

  <div class="contact-band">
    <div class="holder__name">Lukas Varenko</div>
    <div class="holder__title">Fund Manager</div>
    <ul class="contact-list">
      <li>
        <svg viewBox="0 0 16 14" aria-hidden="true"><path d="M1 4c0-2 3-3 7-3s7 1 7 3v1h-3V4H4v1H1zM4 6h8l2 7H2z"/></svg>
        +1 555 284 6190
      </li>
      <li>
        <svg viewBox="0 0 16 14" aria-hidden="true"><path d="M1 2h14v10H1zm1.5 1.2v.3L8 8l5.5-4.5v-.3zM2.5 5.3v5.5h11V5.3L8 9.8z"/></svg>
        lv@FundCorvel.com
      </li>
      <li>
        <svg viewBox="0 0 16 14" aria-hidden="true"><path d="M8 0a7 7 0 1 0 0 14A7 7 0 0 0 8 0zm0 1.3c.9 0 1.8 2 2 4.7H6c.2-2.7 1.1-4.7 2-4.7zM6 7h4c-.2 2.8-1.1 5.7-2 5.7S6.2 9.8 6 7zM2.3 6a5.7 5.7 0 0 1 2.6-4C4.5 3 4.9 5 4.9 6zm0 1h2.6c0 1 .4 3.3.9 4A5.7 5.7 0 0 1 2.3 7zm8.8-1c0-1-.3-3-.9-4a5.7 5.7 0 0 1 3.5 4zm0 1h2.6a5.7 5.7 0 0 1-3.4 4c.5-.7.8-3 .8-4z"/></svg>
        www.FundCorvel.com
      </li>
    </ul>
  </div>
</section>

</body>
</html>
```